Fine Art business needs new website

We need a simple website with a home page, about us page, New sculptures, Sold sculptures, and a contact us page.Our sculptures are very high end one of a kind pieces. As such we need the site to be VERY elegant and professional. Lastly, because I'll be updating pictures on the website on a monthly basis it needs to be user friendly to update (Wordpress is preferred). The only branding we have so far for the business is a business card.
Updates
I wasn't completely ready when this project launched, also I am on the road right now and haven't been able to be as responsive to all you designers as I would like. I will work on giving feedback to all the top designs we've received so far. Thank you all so much for your participation and hardwork.
Target Market(s)
High end customers (affluent), art collectors, interior decorators/designers
Industry/Entity Type
Art Gallery
Coding
Coded - Design and coding required
Number of Pages Required
5+ page
Requirements
Must have
- Easily editable picture gallery for myself so that I can add new pieces(pictures of the pieces), remove sold pieces, etc. I would like the website to be built in wordpress so I can update it. I currently use mangewordpress through Netmarro for my other business website and would like to do the same for this one.
- Pages:
- -Intro page with featured pieces
- -Current pieces gallery (for sale) mainly a picture gallery
- -Sculptures archive (sold pieces) another picture gallery
- -About us: Pull-down of -about the artist (attached content)
- -Artistic Process (attached content)
- -Show Schedule:
- -one page dedicated to "friends of TMV" (basically a link page)
- TO BE CLEAR "www.pineroverslane.com" IS A TOTALLY DIFFERENT SITE AND I'M NOT TRYING TO COMBINE THE TWO OR JOIN THEM INTO ONE. This page needs be more elegant and seperate from the Pine Rovers site.
- UPDATE: I'd like a link to the TMV Facebook page: https://www.faceplume-social.com/mirelcraftworks/
Nice to have
- I would like the pictures on the gallery pages able to have text connected with them (Materials, price)
- I would like the site style and fonts to be similar to our business cards we've already had designed (picture attached).
Should not have
- Too much flash or other things that will make the site slow to load.

```html
<!DOCTYPE html>
<html lang="en">
<head>
<meta charset="utf-8">
<title>Tarnwell Mineral Visions</title>
<link href="https://fonts.googleapis.com/css2?family=Cinzel:wght@400;600&family=Great+Vibes&family=Open+Sans:wght@400;600;700&family=Playfair+Display:wght@400;700&display=swap" rel="stylesheet">
<style>
:root{
  --purple-deep:#2a1640;
  --purple:#3b1f5c;
  --purple-mid:#4e2c78;
  --purple-soft:#6d4a9a;
  --ink:#222;
  --body:#555;
  --white:#fff;
  --grey:#ececec;
  --dark:#1a1a1a;
  --dark-2:#262626;
  --gold:#c9a45c;
}
*{margin:0;padding:0;box-sizing:border-box}
html,body{width:1200px;height:3024px;overflow:hidden}
body{font-family:"Open Sans",sans-serif;color:var(--ink);background:var(--white);position:relative}
.serif{font-family:"Playfair Display",serif}
a{color:inherit;text-decoration:none}

/* header */
.site-header{position:absolute;top:0;left:0;width:1200px;height:144px;background:var(--white)}
.brand{position:absolute;left:40px;top:6px;width:220px;height:130px;display:flex;flex-direction:column;align-items:center;justify-content:center;gap:10px}
.brand-mark{width:150px;height:70px;border-radius:4px;background:linear-gradient(135deg,#2b1b48,#6a4ca0 55%,#1f1530)}
.brand-name{font-family:"Cinzel",serif;font-size:13px;letter-spacing:3px;color:var(--purple)}
.topbar{position:absolute;right:40px;top:12px;display:flex;gap:34px;font-size:13px;color:#666;align-items:center}
.topbar span{display:flex;align-items:center;gap:8px}
.main-nav{position:absolute;right:40px;top:70px;display:flex;gap:40px;font-size:15px;color:#444;align-items:center}

/* hero */
.hero{position:absolute;top:144px;left:0;width:1200px;height:588px;background:linear-gradient(115deg,#1e1030 0%,#3a1f5a 45%,#4d2a73 70%,#2b1745 100%);overflow:hidden}
.hero-art{position:absolute;left:740px;top:40px;width:300px;height:520px;border-radius:140px 60px 120px 40px;background:radial-gradient(ellipse at 50% 40%,#c9b36a 0%,#7a4fb0 35%,#3a1e5e 75%,transparent 100%)}
.hero-copy{position:absolute;left:140px;top:210px;color:var(--white)}
.hero-kicker{font-family:"Great Vibes",cursive;font-size:40px;line-height:1}
.hero-title{font-family:"Cinzel",serif;font-size:44px;letter-spacing:1px;margin-top:6px}
.btn{display:inline-block;background:var(--purple-deep);color:var(--white);font-size:13px;font-weight:700;letter-spacing:2px;padding:12px 26px;border-radius:24px;text-transform:uppercase}
.hero .btn{margin-top:20px;border:1px solid rgba(255,255,255,.5);background:rgba(20,10,35,.6)}
.hero-arrow{position:absolute;top:270px;width:36px;height:36px;border-radius:50%;background:rgba(0,0,0,.35);display:flex;align-items:center;justify-content:center}

/* welcome */
.welcome{position:absolute;top:732px;left:0;width:1200px;height:620px;background:var(--white)}
.welcome-art{position:absolute;left:120px;top:60px;width:280px;height:528px;background:linear-gradient(180deg,#e8e8e8,#cfcfcf);}
.welcome-art::after{content:"";position:absolute;left:70px;top:80px;width:140px;height:360px;border-radius:70px 70px 20px 20px;background:linear-gradient(160deg,#8a5a2e,#3b2414)}
.welcome-copy{position:absolute;left:472px;top:56px;width:690px}
.welcome-copy h2{font-family:"Playfair Display",serif;font-weight:400;font-size:34px;color:var(--ink)}
.welcome-copy h2 b{font-weight:700}
.welcome-copy p{margin-top:18px;font-size:16px;line-height:30px;color:var(--body)}
.welcome-copy .btn{margin-top:36px;margin-left:0}

/* gallery */
.gallery{position:absolute;top:1352px;left:0;width:1200px;height:776px;background:linear-gradient(180deg,var(--dark-2),var(--dark))}
.gallery h2{text-align:center;color:var(--white);font-family:"Playfair Display",serif;font-weight:400;font-size:34px;padding-top:46px}
.gallery h2 b{font-weight:700}
.gallery-intro{width:900px;margin:16px auto 0;text-align:center;font-size:14px;line-height:24px;color:#777}
.cards{position:absolute;top:208px;left:72px;display:flex;gap:24px}
.card{width:248px;text-align:center;color:var(--white)}
.card-img{height:300px;background:#0f0f0f;border:1px solid #333;position:relative}
.card-img i{position:absolute;left:64px;top:24px;width:120px;height:240px;border-radius:60px 60px 16px 16px}
.card h3{font-size:16px;font-weight:600;margin-top:78px;letter-spacing:1px}
.card p{font-size:13px;margin-top:10px;font-weight:600}
.gallery-arrow{position:absolute;top:300px;width:30px;height:44px;background:#3b2257;display:flex;align-items:center;justify-content:center}
.gallery .btn{position:absolute;left:532px;top:692px;background:#111;border:1px solid #666}

/* testimonials */
.testimonials{position:absolute;top:2128px;left:0;width:1200px;height:512px;background:var(--grey)}
.testimonials h2{text-align:center;font-family:"Playfair Display",serif;font-weight:400;font-size:34px;padding-top:60px}
.avatar{position:absolute;left:140px;top:190px;width:100px;height:100px;border-radius:50%;background:linear-gradient(135deg,#b68a6a,#6b4634);border:4px solid var(--white)}
.quote{position:absolute;left:320px;top:180px;width:480px;font-size:16px;line-height:28px;color:#444;font-style:italic}
.quote cite{display:block;margin-top:16px;font-style:normal;font-weight:700}
.test-art{position:absolute;left:820px;top:60px;width:280px;height:440px;background:radial-gradient(ellipse at 50% 45%,#d89a4a 0%,#5a3a7e 40%,#2a1a3a 70%,transparent 72%)}
.test-arrows{position:absolute;left:572px;top:410px;display:flex;gap:20px}

/* footer */
.site-footer{position:absolute;top:2640px;left:0;width:1200px;height:328px;background:var(--purple);color:var(--white)}
.foot-col{position:absolute;top:44px}
.foot-col h4{font-family:"Playfair Display",serif;font-weight:400;font-size:30px}
.quick{left:72px}
.quick ul{list-style:none;margin-top:24px;font-size:13px;line-height:28px}
.quick li::before{content:"›";margin-right:12px}
.newsletter{left:420px}
.newsletter .field{margin-top:30px;width:340px;height:40px;background:var(--white);color:#666;font-size:13px;padding:11px 14px}
.newsletter .btn{margin-top:20px;background:transparent;border:1px solid var(--white);padding:10px 22px}
.socials{display:flex;gap:16px;margin-top:22px}
.socials span{width:18px;height:18px;border-radius:50%;background:rgba(255,255,255,.8)}
.contact{left:872px}
.contact ul{list-style:none;margin-top:28px;font-size:13px;line-height:20px}
.contact li{display:flex;gap:14px;margin-bottom:22px}
.copyright{position:absolute;top:2968px;left:0;width:1200px;height:56px;background:var(--purple-deep);color:#ddd;font-size:12px;display:flex;align-items:center;justify-content:center;gap:8px}
.copyright .page{position:absolute;right:40px;font-size:12px}
</style>
</head>
<body>

<header class="site-header">
  <div class="brand">
    <div class="brand-mark" role="img" aria-label="Purple amethyst geode sculpture emblem"></div>
    <div class="brand-name">Tarnwell Mineral Visions</div>
  </div>
  <div class="topbar">
    <span><svg width="12" height="12" viewBox="0 0 24 24"><path fill="#666" d="M6.6 10.8a15 15 0 006.6 6.6l2.2-2.2c.3-.3.7-.4 1-.2 1.1.4 2.3.6 3.6.6.6 0 1 .4 1 1V20c0 .6-.4 1-1 1A17 17 0 013 4c0-.6.4-1 1-1h3.5c.6 0 1 .4 1 1 0 1.3.2 2.5.6 3.6.1.3 0 .7-.2 1z"/></svg>1-800-555-0142</span>
    <span><svg width="13" height="11" viewBox="0 0 24 18"><rect x="1" y="1" width="22" height="16" fill="none" stroke="#666" stroke-width="2"/><path d="M1 1l11 9 11-9" fill="none" stroke="#666" stroke-width="2"/></svg>info@tarnwellstudio.com</span>
  </div>
  <nav class="main-nav">
    <a>Home</a><a>About Us</a><a>New sculptures</a><a>Sold sculptures</a><a>Contact Us</a>
    <svg width="14" height="14" viewBox="0 0 24 24"><circle cx="10" cy="10" r="7" fill="none" stroke="#444" stroke-width="2.5"/><path d="M15 15l7 7" stroke="#444" stroke-width="2.5"/></svg>
    <svg width="14" height="14" viewBox="0 0 24 24"><circle cx="12" cy="7" r="5" fill="#444"/><path d="M2 23c0-6 5-9 10-9s10 3 10 9z" fill="#444"/></svg>
  </nav>
</header>

<section class="hero">
  <div class="hero-art" role="img" aria-label="Amethyst geode sculpture with golden crystal core on a black base"></div>
  <div class="hero-copy">
    <div class="hero-kicker">Lorem ipsum</div>
    <h1 class="hero-title">TARNWELL MINERAL VISIONS</h1>
    <a class="btn">Learn More</a>
  </div>
  <div class="hero-arrow" style="left:110px"><svg width="12" height="12" viewBox="0 0 10 10"><path d="M7 1L3 5l4 4" fill="none" stroke="#fff" stroke-width="2"/></svg></div>
  <div class="hero-arrow" style="right:110px"><svg width="12" height="12" viewBox="0 0 10 10"><path d="M3 1l4 4-4 4" fill="none" stroke="#fff" stroke-width="2"/></svg></div>
</section>

<section class="welcome">
  <div class="welcome-art" role="img" aria-label="Bronze flowing stone sculpture on a pedestal"></div>
  <div class="welcome-copy">
    <h2>Welcome To <b>Tarnwell Mineral Visions</b></h2>
    <p>Rocks, stones and minerals have been part of our family's story for three generations. What began as a small hobby of collecting crystals on weekend drives grew into a workshop where each find is studied, cut and polished by hand. Every sculpture starts with a single stone and the question of what it wants to become. We pair geodes, agate and quartz with bronze and steel bases so the natural colour and texture can speak for itself. Our children grew up in the studio, learning the craft of shaping stone, and today we work side by side on each piece. We invite you to follow our journey, visit us at upcoming shows and discover a one of a kind work for your home or collection.</p>
    <a class="btn">Read More</a>
  </div>
</section>

<section class="gallery">
  <h2>Our Product <b>Gallery</b></h2>
  <p class="gallery-intro">Lorem ipsum dolor sit amet, consectetur adipiscing elit, sed do eiusmod tempor incididunt ut labore et dolore magna aliqua. Ut enim ad minim veniam, quis nostrud exercitation ullamco laboris.</p>
  <div class="gallery-arrow" style="left:0"><svg width="10" height="12" viewBox="0 0 10 10"><path d="M7 1L3 5l4 4" fill="#fff"/></svg></div>
  <div class="gallery-arrow" style="right:0;background:#999"><svg width="10" height="12" viewBox="0 0 10 10"><path d="M3 1l4 4-4 4" fill="#fff"/></svg></div>
  <div class="cards">
    <div class="card"><div class="card-img" role="img" aria-label="Purple amethyst sculpture"><i style="background:linear-gradient(160deg,#7b4fc0,#2a1450)"></i></div><h3>SCULPTURE-1</h3><p>PRICE : $55.00</p></div>
    <div class="card"><div class="card-img" role="img" aria-label="Green crystal sculpture"><i style="background:linear-gradient(160deg,#5fb07a,#1d4a2b)"></i></div><h3>SCULPTURE-2</h3><p>PRICE : $55.00</p></div>
    <div class="card"><div class="card-img" role="img" aria-label="Blue and gold spiral sculpture"><i style="background:linear-gradient(160deg,#4a5ec0,#c9a45c 60%,#1a2050)"></i></div><h3>SCULPTURE-3</h3><p>PRICE : $55.00</p></div>
    <div class="card"><div class="card-img" role="img" aria-label="Golden amethyst sculpture"><i style="background:linear-gradient(160deg,#e0c27a,#6a4ca0)"></i></div><h3>SCULPTURE-4</h3><p>PRICE : $55.00</p></div>
  </div>
  <a class="btn">View More</a>
</section>

<section class="testimonials">
  <h2>Testimonials</h2>
  <div class="avatar" role="img" aria-label="Client portrait"></div>
  <blockquote class="quote">“Ut enim ad minima veniam, quis nostrum exercitationem ullam corporis suscipit laboriosam, nisi ut aliquid ex ea commodi consequatur”<cite>- Marenka</cite></blockquote>
  <div class="test-art" role="img" aria-label="Amethyst and copper sculpture on a black stand"></div>
  <div class="test-arrows">
    <svg width="14" height="20" viewBox="0 0 10 14"><path d="M8 1L2 7l6 6" fill="none" stroke="#777" stroke-width="1.5"/></svg>
    <svg width="14" height="20" viewBox="0 0 10 14"><path d="M2 1l6 6-6 6" fill="none" stroke="#777" stroke-width="1.5"/></svg>
  </div>
</section>

<footer class="site-footer">
  <div class="foot-col quick">
    <h4>Quick Links</h4>
    <ul><li>Home</li><li>About Us</li><li>New sculptures</li><li>Sold sculptures</li><li>Contact Us</li></ul>
  </div>
  <div class="foot-col newsletter">
    <h4>Newsletter Subscribe</h4>
    <div class="field">Enter Email Id</div>
    <a class="btn">Subscribe</a>
    <div class="socials"><span></span><span></span><span></span></div>
  </div>
  <div class="foot-col contact">
    <h4>Contact us</h4>
    <ul>
      <li><svg width="14" height="16" viewBox="0 0 24 28"><path d="M12 1a9 9 0 00-9 9c0 7 9 17 9 17s9-10 9-17a9 9 0 00-9-9z" fill="#fff"/><circle cx="12" cy="10" r="3.5" fill="#3b1f5c"/></svg><span>412 Quarry Lane,<br>Marlow Ridge, OH 40112</span></li>
      <li><svg width="14" height="14" viewBox="0 0 24 24"><path fill="#fff" d="M6.6 10.8a15 15 0 006.6 6.6l2.2-2.2c.3-.3.7-.4 1-.2 1.1.4 2.3.6 3.6.6.6 0 1 .4 1 1V20c0 .6-.4 1-1 1A17 17 0 013 4c0-.6.4-1 1-1h3.5c.6 0 1 .4 1 1 0 1.3.2 2.5.6 3.6.1.3 0 .7-.2 1z"/></svg><span>1-800-555-0142</span></li>
      <li><svg width="14" height="12" viewBox="0 0 24 18"><rect x="1" y="1" width="22" height="16" fill="none" stroke="#fff" stroke-width="2"/><path d="M1 1l11 9 11-9" fill="none" stroke="#fff" stroke-width="2"/></svg><span>contact@tarnwellstudio.com</span></li>
    </ul>
  </div>
</footer>
<div class="copyright">© 2018 | www.tarnwellstudio.com<span class="page">1/1</span></div>

</body>
</html>
```